Business Card Design for company

We want new business cards. We'd like something different-- yet still highly professional. Our tagline is Providing leadership, delivering success. Stock photos are ok, as long as they are relevant and look upscale.

Target Market(s)

Architecture/Business Management Consulting/Engineering Consulting

Contact Information for Business Card

dark gray background with pops of blue might be good, but you tell me. You're the designers. Rounded corners might be nice, but again, you tell me.

Font styles to use
Serif
Sans Serif

Colors
3276b5
5c5c5c
9d9d9d
fbfbfb

Requirements
Nice to have
• Something different, but still very professional.

```html
<!DOCTYPE html>
<html lang="en">
<head>
<meta charset="utf-8">
<title>Norvane Partners – Business Card</title>
<link rel="stylesheet" href="https://fonts.googleapis.com/css2?family=Roboto:wght@400;500;700&display=swap">
<style>
  :root {
    --backdrop: #1f1f20;
    --paper: #ffffff;
    --slate: #4a4d52;
    --brand-blue: #2a6499;
    --text-gray: #55585c;
    --title-gray: #4d5055;
    --on-dark: #ffffff;
  }
  * { margin: 0; padding: 0; box-sizing: border-box; }
  html, body { width: 1125px; height: 1200px; overflow: hidden; }
  body {
    background: var(--backdrop);
    font-family: "Roboto", Arial, sans-serif;
    position: relative;
  }
  .card {
    position: absolute;
    left: 150px;
    width: 825px;
    height: 471px;
  }
  .card-front { top: 98px; background: var(--paper); }
  .card-back { top: 631px; background: var(--slate); }

  .wordmark {
    position: absolute;
    left: 53px;
    top: 46px;
    color: var(--brand-blue);
    font-weight: 700;
    font-size: 64px;
    line-height: 1.02;
    letter-spacing: 1px;
  }
  .address {
    position: absolute;
    left: 53px;
    top: 241px;
    color: var(--text-gray);
    font-size: 20px;
    line-height: 25px;
  }
  .contact-list {
    position: absolute;
    left: 53px;
    top: 305px;
    list-style: none;
    color: var(--text-gray);
    font-size: 20px;
    line-height: 26px;
  }
  .contact-list li { display: flex; align-items: center; gap: 12px; }
  .contact-list svg { width: 20px; height: 20px; fill: var(--brand-blue); flex: none; }

  .person {
    position: absolute;
    right: 53px;
    top: 308px;
    text-align: right;
  }
  .person-name {
    color: var(--brand-blue);
    font-weight: 700;
    font-size: 30px;
    line-height: 32px;
  }
  .person-title {
    color: var(--title-gray);
    font-weight: 500;
    font-size: 20px;
    line-height: 26px;
  }
  .accent-bar {
    position: absolute;
    bottom: 0;
    height: 13px;
  }
  .accent-blue { left: 0; width: 512px; background: var(--brand-blue); }
  .accent-slate { left: 516px; right: 0; background: var(--slate); }

  .back-name {
    position: absolute;
    left: 0; right: 0;
    top: 160px;
    text-align: center;
    color: var(--on-dark);
    font-weight: 500;
    font-size: 112px;
    line-height: 1;
    letter-spacing: 2px;
  }
  .tagline {
    position: absolute;
    left: 0; right: 0;
    top: 395px;
    text-align: center;
    color: var(--on-dark);
    font-size: 21px;
  }
  .tagline .dot {
    display: inline-block;
    width: 8px; height: 8px;
    border-radius: 50%;
    background: var(--on-dark);
    margin: 0 12px;
    vertical-align: middle;
  }
</style>
</head>
<body>
  <section class="card card-front">
    <div class="wordmark">NORVANE<br>PARTNERS</div>
    <p class="address">4120 Juniper Court<br>Fairbanks, Alaska 99701</p>
    <ul class="contact-list">
      <li><svg viewBox="0 0 20 20"><path d="M5 2l3 4-2 2c1 2 3 4 6 6l2-2 4 3-2 3C9 18 2 11 2 4z"/></svg>907 555 0142</li>
      <li><svg viewBox="0 0 20 20"><path d="M6 1h8a1 1 0 011 1v16a1 1 0 01-1 1H6a1 1 0 01-1-1V2a1 1 0 011-1zm1 2v12h6V3zm3 13a1 1 0 100 2 1 1 0 000-2z"/></svg>907 555 0187</li>
      <li><svg viewBox="0 0 20 20"><path d="M5 2h10v5H5zM2 8h16v8h-3v2H5v-2H2zm4 5v4h8v-4z"/></svg>907 555 0163</li>
      <li><svg viewBox="0 0 20 20"><path d="M2 5h16v11H2zm1.5 1.5v.4L10 11l6.5-4.1v-.4zm0 2.2v5.8h13V8.7L10 12.8z"/></svg>daniel@norvanepartners.com</li>
      <li><svg viewBox="0 0 20 20"><path d="M10 2a8 8 0 100 16 8 8 0 000-16zm-1 2.2c-1 1-1 2 0 3s2 0 2 2-2 1-3 3 1 3 0 4.4A6 6 0 014 10a6 6 0 015-5.8zm3 .3a6 6 0 013.8 8c-1-.6-2-.2-2.8-1.3s.5-2.3-.8-3.2S11 6 12 4.5z"/></svg>www.norvanepartners.com</li>
    </ul>
    <div class="person">
      <div class="person-name">DANIEL HART</div>
      <div class="person-title">CEO/FOUNDER</div>
    </div>
    <div class="accent-bar accent-blue"></div>
    <div class="accent-bar accent-slate"></div>
  </section>

  <section class="card card-back">
    <div class="back-name">NORVANE</div>
    <p class="tagline">Providing leadership<span class="dot"></span>delivering success</p>
  </section>
</body>
</html>
```